Naturopath Practitioner Card Design

I am a naturopath needing a design for a business card mainly to show that I am a naturopath and have some contact details to give to prospective clients. I am open minded about the design and what is on the second side of the card whether it just be some artwork or space for details, appointment times etc. Naturopathy is the practice of natural medicine that uses a holistic approach and incorporates herbal and nutritional medicine.

Industry/Entity Type

Business

Contact Information for Business Card

Tom Rudd NaturopathBHSc (Naturopathy) Member WHPG 0487 925 316 tom.rudd@mailexample.com www.tomruddnaturopathy.example.au

Requirements
Nice to have
• Would prefer some kind of original pattern/art work/logo rather than an image, not fussed if its very simple/basic
• I am open to any colour but think I would prefer a more earthy sandy clay etc type style than the greens that are commonly associated with naturopathy.
Should not have
• Don't really want to have generic stock images on it

```html
<!DOCTYPE html>
<html lang="en">
<head>
<meta charset="utf-8">
<title>Tom Rudd Naturopath – Business Card</title>
<link rel="stylesheet" href="https://fonts.googleapis.com/css2?family=Source+Sans+3:ital,wght@0,400;0,600;1,700&display=swap">
<style>
  :root {
    --backdrop-top: #2a2a2a;
    --backdrop-bottom: #050505;
    --card: #ffffff;
    --green-light: #7de21f;
    --green-mid: #4cb814;
    --green-dark: #1f7a12;
    --text-grey: #3d3d3d;
    --rule-grey: #6a6a6a;
    --headline: #111111;
    --note-navy: #1d2540;
  }
  * { box-sizing: border-box; margin: 0; padding: 0; }
  html, body { width: 1200px; height: 900px; overflow: hidden; }
  body {
    position: relative;
    background: linear-gradient(180deg, var(--backdrop-top) 0%, #161616 55%, var(--backdrop-bottom) 100%);
    font-family: "Source Sans 3", "Myriad Pro", sans-serif;
  }
  .card {
    position: absolute;
    top: 170px;
    width: 347px;
    height: 561px;
    background: var(--card);
    overflow: hidden;
  }
  .card--front { left: 259px; }
  .card--back { left: 631px; }

  /* Front */
  .tab {
    position: absolute;
    left: 102px;
    width: 143px;
    background: linear-gradient(180deg, var(--green-light) 0%, var(--green-mid) 55%, var(--green-dark) 100%);
  }
  .tab--top { top: 0; height: 30px; }
  .tab--bottom { bottom: 0; height: 28px; }

  .identity {
    position: absolute;
    top: 174px;
    left: 0;
    width: 100%;
    text-align: center;
    color: var(--text-grey);
  }
  .identity__name {
    font-size: 32px;
    font-weight: 600;
    line-height: 36px;
    letter-spacing: 0.2px;
    background: linear-gradient(180deg, var(--green-light) 0%, var(--green-mid) 50%, var(--green-dark) 100%);
    -webkit-background-clip: text;
    background-clip: text;
    color: transparent;
  }
  .identity__role { font-size: 19px; line-height: 24px; margin-top: 2px; }
  .identity__credentials { font-size: 19px; line-height: 24px; margin-top: 10px; }

  .contact {
    position: absolute;
    top: 334px;
    left: 0;
    width: 100%;
    display: flex;
    flex-direction: column;
    align-items: center;
    color: var(--text-grey);
    font-size: 19px;
    line-height: 25px;
  }
  .contact__item { display: flex; align-items: center; gap: 7px; }
  .contact__icon { width: 14px; height: 14px; flex: none; }

  /* Back */
  .appointment {
    position: absolute;
    width: 561px;
    height: 347px;
    left: -107px;
    top: 107px;
    transform: rotate(-90deg);
    color: var(--headline);
  }
  .appointment__title {
    position: absolute;
    left: 146px;
    top: 67px;
    font-size: 24px;
    font-weight: 600;
    line-height: 28px;
    white-space: nowrap;
  }
  .field-label {
    position: absolute;
    left: 83px;
    font-size: 15px;
    line-height: 16px;
    white-space: nowrap;
  }
  .field-rule {
    position: absolute;
    height: 1px;
    background: var(--rule-grey);
  }
  .field-unit {
    position: absolute;
    font-size: 15px;
    line-height: 16px;
  }
  .appointment__note {
    position: absolute;
    left: 91px;
    top: 255px;
    font-size: 14px;
    font-weight: 700;
    font-style: italic;
    color: var(--note-navy);
    white-space: nowrap;
  }
</style>
</head>
<body>
  <section class="card card--front" aria-label="Card front">
    <div class="tab tab--top"></div>
    <div class="identity">
      <h1 class="identity__name">TOM RUDD</h1>
      <p class="identity__role">Naturopath</p>
      <p class="identity__credentials">BHSc (Naturopathy) Member WHPG</p>
    </div>
    <div class="contact">
      <p class="contact__item">
        <svg class="contact__icon" viewBox="0 0 16 16" aria-hidden="true">
          <path fill="#3aa516" d="M3.6 1.2l2.3 2.6c.3.4.3.9 0 1.3L4.7 6.4c.8 1.9 2.9 4 4.9 4.9l1.3-1.2c.4-.3.9-.3 1.3 0l2.6 2.3c.4.3.4.9 0 1.3l-1.3 1.3c-.7.7-1.8.9-2.7.5C6.5 14 2 9.5.5 5.2.1 4.3.3 3.2 1 2.5l1.3-1.3c.4-.4 1-.4 1.3 0z"/>
        </svg>
        <span>0487 925 316</span>
      </p>
      <p class="contact__item">
        <svg class="contact__icon" viewBox="0 0 16 16" aria-hidden="true">
          <rect x="1" y="3.5" width="14" height="9" fill="#3aa516"/>
          <path d="M1.5 4l6.5 5 6.5-5" fill="none" stroke="#ffffff" stroke-width="1.2"/>
        </svg>
        <span>tom.rudd@mailexample.com</span>
      </p>
    </div>
    <div class="tab tab--bottom"></div>
  </section>

  <section class="card card--back" aria-label="Card back">
    <div class="appointment">
      <h2 class="appointment__title">Your Next Appointment is</h2>

      <span class="field-label" style="top:131px">Name :</span>
      <span class="field-rule" style="left:141px; top:139px; width:322px"></span>

      <span class="field-label" style="top:171px">Date :</span>
      <span class="field-rule" style="left:141px; top:179px; width:322px"></span>

      <span class="field-label" style="top:207px">Time:</span>
      <span class="field-rule" style="left:141px; top:215px; width:116px"></span>
      <span class="field-unit" style="left:259px; top:207px">AM</span>
      <span class="field-rule" style="left:294px; top:215px; width:160px"></span>
      <span class="field-unit" style="left:457px; top:207px">PM</span>

      <p class="appointment__note">If unable to keep appointment, kindly give 24hrs notice.</p>
    </div>
  </section>
</body>
</html>
```